need corporate, modern business card created for Consulting Company

I need a slick business card using elements from my website, as well as, integrating my pixelforge-created logo (see files).

The business card needs to be:
1. Corporate and modern
2. Clean and professional

I've included a PSD with the logo/icon that you can use to create it. Feel free to try a metallic finish on the logo, make it bigger/small, underlay it. Whatever you need to do to make my card stand out.

Try a black background, or white background or gray.

The idea is for my card to be memorable as well as professional and corporate.

Target Market(s)

Corporate business in the US and Canada.

Industry/Entity Type

Business

Contact Information for Business Card

Commerce Advancing Methods
Martin Coles, Senior Partner
office: 1 877 555 0143
mobile: 1 519 555 0172
website: http://www.brightvale.example

Requirements
Must have
• Card-related information
• corporate, yet modern
• clean and professional
• incorporate the icon only
• must have an editable form when complete!
Nice to have
• metallic icon might be cool
• try it with white or black

```html
<!DOCTYPE html>
<html lang="en">
<head>
<meta charset="utf-8">
<title>Brightvale Business Card</title>
<link rel="stylesheet" href="https://fonts.googleapis.com/css2?family=Comfortaa:wght@400;700&family=Roboto+Condensed:wght@400;700&display=swap">
<style>
  :root {
    --backdrop: #d6caca;
    --card-black: #141518;
    --card-edge: #2a2c31;
    --accent-blue: #2f6bbd;
    --accent-blue-light: #6f8fb8;
    --text-white: #f2f2f2;
    --text-blue: #3b78cf;
    --silver-light: #f4f4f4;
    --silver-mid: #a9abae;
    --silver-dark: #5d5f63;
  }
  html, body {
    margin: 0;
    width: 1200px;
    height: 800px;
    overflow: hidden;
    background: var(--backdrop);
  }
  .stage {
    position: relative;
    width: 1200px;
    height: 800px;
  }
  .card {
    position: absolute;
    top: 100px;
    width: 360px;
    height: 600px;
    border-radius: 22px;
    overflow: hidden;
    background: radial-gradient(ellipse at 50% 40%, #2a2c30 0%, var(--card-black) 70%);
    box-shadow: 0 0 0 1px var(--card-edge);
  }
  .card--front { left: 170px; }
  .card--back  { left: 670px; }

  /* Landscape content rotated to read down the portrait card */
  .card__content {
    position: absolute;
    width: 600px;
    height: 360px;
    left: 0;
    top: 0;
    transform-origin: 0 0;
    transform: translate(360px, 0) rotate(90deg);
  }

  .front__corner {
    position: absolute;
    left: 0;
    top: 0;
    width: 600px;
    height: 360px;
  }

  .wordmark {
    font-family: "Comfortaa", sans-serif;
    font-weight: 700;
    letter-spacing: 1px;
    display: flex;
    align-items: center;
    gap: 12px;
  }
  .wordmark__square {
    width: 22px;
    height: 22px;
    border-radius: 3px;
  }
  .front__wordmark {
    position: absolute;
    left: 30px;
    top: 235px;
    font-size: 44px;
    color: var(--text-blue);
  }
  .front__wordmark .wordmark__square { background: var(--text-blue); }

  .front__divider {
    position: absolute;
    left: 312px;
    top: 30px;
    width: 2px;
    height: 300px;
    background: var(--accent-blue);
  }

  .contact {
    position: absolute;
    left: 335px;
    top: 40px;
    width: 250px;
  }
  .contact__name {
    font-family: "Comfortaa", sans-serif;
    font-size: 34px;
    font-weight: 400;
    color: var(--text-white);
    margin: 0;
    white-space: nowrap;
  }
  .contact__title {
    font-family: "Roboto Condensed", sans-serif;
    font-weight: 700;
    font-size: 13px;
    letter-spacing: 1px;
    color: var(--text-blue);
    margin: 6px 0 14px;
  }
  .contact__list {
    list-style: none;
    margin: 0;
    padding: 0;
    font-family: "Roboto Condensed", sans-serif;
    font-size: 17px;
    letter-spacing: 1px;
    color: var(--text-white);
  }
  .contact__list li {
    display: flex;
    align-items: center;
    gap: 9px;
    height: 32px;
    white-space: nowrap;
  }
  .contact__list .contact__web { color: var(--text-blue); font-size: 16px; }
  .contact__icon { width: 15px; height: 15px; flex: none; }

  .back__glow {
    position: absolute;
    left: 20px;
    top: 50px;
    width: 300px;
    height: 300px;
    border-radius: 50%;
    background: radial-gradient(circle, rgba(255,255,255,0.07) 0%, rgba(255,255,255,0) 70%);
  }
  .back__mark {
    position: absolute;
    left: 70px;
    top: 100px;
    width: 190px;
    height: 190px;
    border-radius: 16px;
    background: linear-gradient(135deg, var(--silver-light) 0%, var(--silver-mid) 45%, var(--silver-dark) 70%, var(--silver-mid) 100%);
  }
  .back__wordmark {
    position: absolute;
    left: 300px;
    top: 250px;
    font-size: 40px;
    color: var(--text-white);
  }
</style>
</head>
<body>
<main class="stage">

  <section class="card card--front" aria-label="Card front">
    <div class="card__content">
      <svg class="front__corner" viewBox="0 0 600 360" aria-hidden="true">
        <polygon points="0,0 300,0 0,150" fill="var(--accent-blue)"/>
        <polygon points="300,0 314,0 0,157 0,150" fill="var(--accent-blue-light)"/>
      </svg>

      <div class="wordmark front__wordmark">
        <span class="wordmark__square"></span>brightvale
      </div>

      <div class="front__divider"></div>

      <div class="contact">
        <h1 class="contact__name">Martin Coles</h1>
        <p class="contact__title">Senior Partner</p>
        <ul class="contact__list">
          <li>
            <svg class="contact__icon" viewBox="0 0 16 16"><rect x="1" y="3" width="14" height="10" rx="2" fill="var(--accent-blue)"/><circle cx="8" cy="8" r="2.5" fill="var(--card-black)"/></svg>
            1 877 555 0143
          </li>
          <li>
            <svg class="contact__icon" viewBox="0 0 16 16"><rect x="4" y="1" width="8" height="14" rx="1.5" fill="none" stroke="var(--accent-blue)" stroke-width="1.6"/></svg>
            1 519 555 0172
          </li>
          <li>
            <svg class="contact__icon" viewBox="0 0 16 16"><rect x="1" y="3" width="14" height="10" rx="1" fill="var(--accent-blue)"/><path d="M1 4 L8 9 L15 4" fill="none" stroke="var(--card-black)" stroke-width="1.4"/></svg>
            info@brightvale.example
          </li>
          <li class="contact__web">
            <svg class="contact__icon" viewBox="0 0 16 16"><circle cx="8" cy="8" r="6.5" fill="var(--accent-blue)"/><path d="M1.5 8 H14.5 M8 1.5 C4 5 4 11 8 14.5 M8 1.5 C12 5 12 11 8 14.5" fill="none" stroke="var(--card-black)" stroke-width="1"/></svg>
            www.brightvale.example
          </li>
        </ul>
      </div>
    </div>
  </section>

  <section class="card card--back" aria-label="Card back">
    <div class="card__content">
      <div class="back__glow" aria-hidden="true"></div>
      <div class="back__mark" role="img" aria-label="Large metallic brand mark"></div>
      <div class="wordmark back__wordmark">brightvale</div>
    </div>
  </section>

</main>
</body>
</html>
```